Professional Package for CPA Firm

We would like a stationery design for our new CPA Firm based in Atlanta, GA called 'Vale 8'. We work with investors to help grow investments, tax free. We would like the design to have a professional/minimal look with a 'wow' factor. We need 9.5″ x 4.125″, 9x12, and 10x13 mailing envelopes, business cards, and a letterhead. We have a logo that is already complete. For the letterhead, we would like to have space to put credentials at the bottom of the page

Industry/Entity Type

CPA, Accounting

```html
<!DOCTYPE html>
<html lang="en">
<head>
<meta charset="utf-8">
<title>Vale 8 — Business Cards</title>
<link href="https://fonts.googleapis.com/css2?family=Open+Sans:wght@400;600;700&display=swap" rel="stylesheet">
<style>
  :root {
    --backdrop: #1f2022;
    --card-navy: #0e3350;
    --accent-teal: #22b8c4;
    --accent-coral: #f0555a;
    --text-light: #ffffff;
    --text-muted: #d8e2ea;
  }
  * { margin: 0; padding: 0; box-sizing: border-box; }
  html, body { width: 1200px; height: 874px; overflow: hidden; }
  body {
    background: var(--backdrop);
    font-family: "Open Sans", sans-serif;
    position: relative;
  }
  .card {
    position: absolute;
    width: 620px;
    height: 354px;
    background: var(--card-navy);
    border-radius: 22px;
    box-shadow: 0 10px 30px rgba(0,0,0,0.45);
    overflow: hidden;
  }
  .card--front { left: 500px; top: 56px; }
  .card--back { left: 80px; top: 460px; }

  .brand {
    display: flex;
    align-items: center;
    gap: 12px;
  }
  .brand__dot {
    width: 18px; height: 18px;
    border-radius: 50%;
    background: var(--accent-coral);
  }
  .brand__name {
    font-weight: 700;
    color: var(--text-light);
    letter-spacing: 2px;
  }
  .brand__tagline {
    color: var(--text-muted);
    letter-spacing: 2px;
  }

  .card--front .brand-block {
    position: absolute;
    left: 0; right: 0; top: 118px;
    display: flex; flex-direction: column; align-items: center; gap: 10px;
  }
  .card--front .brand__name { font-size: 56px; color: #c9ccd0; }
  .card--front .brand__tagline { font-size: 15px; color: #9aa4ad; }

  .card--back .brand-block {
    position: absolute;
    left: 40px; top: 50px;
    display: flex; flex-direction: column; gap: 6px;
  }
  .card--back .brand__name { font-size: 44px; }
  .card--back .brand__tagline { font-size: 12px; }

  .divider {
    position: absolute;
    left: 40px; right: 40px; top: 196px;
    height: 1px;
    background: var(--accent-teal);
  }
  .address {
    position: absolute;
    left: 40px; top: 214px;
    font-size: 14px;
    line-height: 1.45;
    color: var(--text-light);
  }
  .person {
    position: absolute;
    right: 40px; top: 210px;
    text-align: right;
  }
  .person__name {
    font-size: 19px;
    font-weight: 600;
    color: var(--accent-teal);
    letter-spacing: 0.5px;
  }
  .person__title {
    font-size: 14px;
    color: var(--accent-coral);
  }
  .person__rule {
    height: 1px;
    width: 170px;
    background: var(--accent-teal);
    margin: 8px 0 8px auto;
  }
  .contact {
    list-style: none;
    font-size: 14px;
    color: var(--text-light);
    line-height: 1.5;
  }
  .contact li {
    display: flex; align-items: center; justify-content: flex-end; gap: 10px;
  }
  .contact svg { width: 12px; height: 12px; fill: var(--accent-coral); }
</style>
</head>
<body>

<section class="card card--front" aria-label="Business card front">
  <div class="brand-block">
    <div class="brand">
      <span class="brand__name">VALE 8</span>
    </div>
    <span class="brand__tagline">CPAs and Tax Advisors</span>
  </div>
</section>

<section class="card card--back" aria-label="Business card back">
  <div class="brand-block">
    <div class="brand">
      <span class="brand__name">VALE 8</span>
      <span class="brand__dot"></span>
    </div>
    <span class="brand__tagline">CPAs and Tax Advisors</span>
  </div>

  <div class="divider"></div>

  <address class="address" style="font-style: normal;">
    412 Birchwood Court<br>
    Atlanta, Georgia 30318<br>
    www.vale8.com
  </address>

  <div class="person">
    <div class="person__name">DANIEL WARD</div>
    <div class="person__title">President</div>
    <div class="person__rule"></div>
    <ul class="contact">
      <li>404-555-0182
        <svg viewBox="0 0 24 24" aria-hidden="true"><path d="M6.6 10.8a15.1 15.1 0 0 0 6.6 6.6l2.2-2.2a1 1 0 0 1 1-.25 11.4 11.4 0 0 0 3.6.6 1 1 0 0 1 1 1V20a1 1 0 0 1-1 1A17 17 0 0 1 3 4a1 1 0 0 1 1-1h3.5a1 1 0 0 1 1 1c0 1.25.2 2.45.6 3.6a1 1 0 0 1-.25 1z"/></svg>
      </li>
      <li>404-555-0147
        <svg viewBox="0 0 24 24" aria-hidden="true"><path d="M7 1h10a2 2 0 0 1 2 2v18a2 2 0 0 1-2 2H7a2 2 0 0 1-2-2V3a2 2 0 0 1 2-2zm0 3v14h10V4zm5 15.5a1 1 0 1 0 0 2 1 1 0 0 0 0-2z"/></svg>
      </li>
      <li>info@vale8.com
        <svg viewBox="0 0 24 24" aria-hidden="true"><path d="M2 5h20v14H2zm2 2v.5l8 5 8-5V7zm0 2.8V17h16V9.8l-8 5z"/></svg>
      </li>
    </ul>
  </div>
</section>

</body>
</html>
```